Business Cards for IT Consulting Company (Managed Service Provider)

I am looking to have some business cards printed and would like some designs. We are an IT Consulting company based in Vancouver BC. I would like a nice clean and modern look to the cards. I have uploaded all the versions of my logo so parts can be used as needed. Here is a snippit from our website homepage:

Quillbrook Networks Ltd. is an IT Solutions Partner located in Vancouver BC, Canada. We offer IT solutions and support to customers in the greater Vancouver Area. With expertise in Microsoft platforms, as well as Linux and Mac OSX and over 12 years experience in the IT industry, Quillbrook Networks is dedicated to offering our clients top quality service and products. We take pride in the solutions we offer our customers. The greatest compliment a client can give us is to recommend our services.

Quillbrook Networks Ltd. offers a wide range of IT services from onsite service to remote support and managed service solutions. This allows clients to choose the support path that best suits their company’s needs. Supporting many different sized companies from small to enterprise level over the past 12 years Quillbrook Networks has the experience and expertise needed to ensure things run smoothly. Allowing our clients to focus on doing business.

Revolutionizing the way IT services are delivered.

Quillbrook Networks is dedicated to providing our clients with IT solutions that work and grow with them for years to come. This philosophy helps save money in the long run instead of replacing equipment constantly. Far too often IT solutions are not well thought out and while possibly solving the problem at hand, require replacement due to growth or quality within a very short time frame. Quillbrook Networks takes pride in providing solutions that will last and be able to accommodate growth without the need for replacement.

Industry/Entity Type

Information Technology

Contact Information for Business Card

Quillbrook Networks Ltd.
(Employee Name)
Eml: (Employees Email Address)
Web: quillbrook.me
Ph: 604-555-0148

Font styles to use
Serif
Sans Serif

Requirements
Must have
• The Company logo and company colors.
Nice to have
• - Our tag line: "Rethinking the Way IT Works" or "Revolutionizing the way IT services are delivered."
• - Also I really like the idea of nature and technology together blending which is sort of where my logo came from so integrating that somehow onto the business cards would be great.

```html
<!DOCTYPE html>
<html lang="en">
<head>
<meta charset="utf-8">
<title>Quillbrook Networks Ltd. – Business Card</title>
<link rel="stylesheet" href="https://fonts.googleapis.com/css2?family=Open+Sans:wght@400;600;700&display=swap">
<style>
  :root {
    --stage: #3c3c3e;
    --card-white: #ffffff;
    --brand-blue: #0aa1de;
    --panel-grey: #606163;
    --ink-grey: #58595b;
    --text-light: #ffffff;
  }
  * { box-sizing: border-box; margin: 0; padding: 0; }
  html, body {
    width: 1105px;
    height: 1200px;
    overflow: hidden;
  }
  body {
    background: var(--stage);
    font-family: "Open Sans", Arial, sans-serif;
    position: relative;
  }
  .card {
    position: absolute;
    left: 194px;
    width: 720px;
    height: 412px;
    overflow: hidden;
  }
  .card-front { top: 146px; background: var(--card-white); }
  .card-back  { top: 602px; background: var(--brand-blue); }

  .front-shape {
    position: absolute;
    inset: 0;
    width: 100%;
    height: 100%;
  }
  .brand {
    position: absolute;
    left: 54px;
    top: 82px;
    display: flex;
    align-items: center;
    gap: 14px;
  }
  .brand-square {
    width: 34px;
    height: 34px;
    background: var(--brand-blue);
  }
  .brand-name {
    font-size: 26px;
    font-weight: 600;
    color: var(--ink-grey);
    letter-spacing: 0.2px;
  }
  .contact {
    position: absolute;
    right: 40px;
    top: 190px;
    text-align: right;
    color: var(--text-light);
  }
  .contact-name {
    font-size: 29px;
    font-weight: 600;
    margin-bottom: 14px;
    letter-spacing: 0.3px;
  }
  .contact-address {
    font-size: 18px;
    line-height: 27px;
    margin-bottom: 6px;
  }
  .contact-line {
    display: flex;
    justify-content: flex-end;
    align-items: center;
    gap: 12px;
    font-size: 18px;
    line-height: 29px;
  }
  .contact-icon {
    width: 18px;
    height: 18px;
    flex: none;
  }

  .back-pattern {
    position: absolute;
    inset: 0;
    background: linear-gradient(135deg, #12a6e0 0%, #0a9cd8 100%);
  }
  .back-brand {
    position: absolute;
    left: 0;
    right: 0;
    top: 192px;
    text-align: center;
    font-size: 26px;
    font-weight: 600;
    color: var(--text-light);
  }
  .tagline {
    position: absolute;
    left: 0;
    right: 0;
    top: 324px;
    text-align: center;
    font-size: 19px;
    font-weight: 600;
    color: var(--text-light);
  }
</style>
</head>
<body>

  <section class="card card-front">
    <svg class="front-shape" viewBox="0 0 720 412" aria-hidden="true">
      <polygon points="466,0 720,0 720,412 298,412 512,70" fill="var(--brand-blue)"/>
      <polygon points="480,0 720,0 720,412 312,412 526,70" fill="var(--panel-grey)"/>
    </svg>

    <div class="brand">
      <span class="brand-square"></span>
      <span class="brand-name">Quillbrook Networks Ltd.</span>
    </div>

    <div class="contact">
      <p class="contact-name">Daniel Hartley</p>
      <p class="contact-address">2140 Alder Crescent<br>Vancouver, BC V5K 2R7</p>
      <p class="contact-line">604-555-0148
        <svg class="contact-icon" viewBox="0 0 24 24" aria-hidden="true">
          <path fill="#fff" d="M6.6 10.8c1.4 2.8 3.8 5.1 6.6 6.6l2.2-2.2c.3-.3.7-.4 1-.2 1.1.4 2.3.6 3.6.6.6 0 1 .4 1 1V20c0 .6-.4 1-1 1C10.6 21 3 13.4 3 4c0-.6.4-1 1-1h3.5c.6 0 1 .4 1 1 0 1.3.2 2.5.6 3.6.1.3 0 .7-.2 1z"/>
        </svg>
      </p>
      <p class="contact-line">dhartley@quillbrook.me
        <svg class="contact-icon" viewBox="0 0 24 24" aria-hidden="true">
          <rect x="2" y="5" width="20" height="14" fill="#fff"/>
          <path d="M2 5l10 8 10-8" fill="none" stroke="var(--panel-grey)" stroke-width="1.6"/>
        </svg>
      </p>
      <p class="contact-line">www.quillbrook.me
        <svg class="contact-icon" viewBox="0 0 24 24" aria-hidden="true">
          <circle cx="12" cy="12" r="10" fill="#fff"/>
          <path d="M7 8c2 0 3 1 3 3s-2 2-2 4M14 5c0 2 2 2 3 3s-1 3 0 4 2 1 2 3" fill="none" stroke="var(--panel-grey)" stroke-width="1.8"/>
        </svg>
      </p>
    </div>
  </section>

  <section class="card card-back">
    <div class="back-pattern" role="img" aria-label="Faint repeating hexagon pattern across the blue background"></div>
    <p class="back-brand">Quillbrook Networks Ltd.</p>
    <p class="tagline">Rethinking the Way IT Works</p>
  </section>

</body>
</html>
```